"Harbor Builders" is a residential building company and needs a new business card design and may re

We would like a redesign based on the existing logo, and would like to see a new font as well. We are bespoke home builders who build sustainable energy efficient homes.

Industry/Entity Type

Construction

Contact Information for Business Card

Business card size 40mm x 90mm

Colors

Designer to choose colors to be used in the design.

```html
<!DOCTYPE html>
<html lang="en">
<head>
<meta charset="utf-8">
<title>Harbor Builders – Business Card</title>
<link rel="stylesheet" href="https://fonts.googleapis.com/css2?family=Montserrat:wght@300;400;700&family=Open+Sans:wght@400&display=swap">
<style>
  :root {
    --backdrop: #2c2c2c;
    --card-light: #ffffff;
    --card-dark: #1e1e1e;
    --ink: #3b3b3d;
    --ink-soft: #4a4a4c;
    --accent: #9cc83a;
    --mark-grey: #5a5a5c;
    --mark-light: #d6d6d6;
  }
  * { box-sizing: border-box; margin: 0; padding: 0; }
  html, body { width: 1058px; height: 1200px; overflow: hidden; }
  body {
    background: var(--backdrop);
    font-family: "Open Sans", Arial, sans-serif;
    display: flex;
    flex-direction: column;
    align-items: center;
    justify-content: center;
    gap: 70px;
  }
  .card {
    position: relative;
    width: 880px;
    height: 391px;
    box-shadow: 0 10px 30px rgba(0,0,0,.35);
  }
  .card--front { background: var(--card-light); color: var(--ink); }
  .card--back {
    background: var(--card-dark);
    display: flex;
    align-items: center;
    justify-content: center;
  }

  .brand {
    display: flex;
    align-items: center;
    gap: 16px;
    font-family: "Montserrat", Arial, sans-serif;
    font-weight: 300;
    white-space: nowrap;
  }
  .brand__square { display: block; }
  .brand--front { position: absolute; top: 64px; right: 60px; }
  .brand--front .brand__square { width: 44px; height: 44px; background: var(--mark-grey); }
  .brand--front .brand__name { font-size: 40px; color: var(--ink-soft); }
  .brand--back .brand__square { width: 80px; height: 80px; background: var(--mark-light); }
  .brand--back .brand__name { font-size: 68px; color: var(--mark-light); }

  .person { position: absolute; left: 50px; top: 150px; }
  .person__name {
    font-family: "Montserrat", Arial, sans-serif;
    font-weight: 300;
    font-size: 34px;
    color: var(--ink-soft);
    letter-spacing: .3px;
  }
  .person__name strong { font-weight: 700; }
  .person__phone { font-size: 29px; color: var(--ink); margin-top: 2px; }

  .contacts {
    position: absolute;
    left: 50px;
    bottom: 28px;
    list-style: none;
    font-size: 20px;
    color: var(--ink);
    line-height: 1.55;
  }
  .contacts__item { display: flex; align-items: center; gap: 14px; }
  .contacts__icon { width: 20px; height: 20px; flex: none; }
  .contacts__legal { color: var(--accent); margin-top: 6px; }
</style>
</head>
<body>
  <section class="card card--front" aria-label="Business card front">
    <div class="brand brand--front">
      <span class="brand__square"></span>
      <span class="brand__name">Harbor Builders</span>
    </div>

    <div class="person">
      <p class="person__name">Daniel <strong>Moretti</strong></p>
      <p class="person__phone">0400 555 018</p>
    </div>

    <ul class="contacts">
      <li class="contacts__item">
        <svg class="contacts__icon" viewBox="0 0 20 20" aria-hidden="true">
          <rect x="1" y="4" width="18" height="12" fill="var(--accent)"/>
          <path d="M1 4 L10 11 L19 4" fill="none" stroke="#fff" stroke-width="1.5"/>
        </svg>
        <span>daniel@harborbuilders.example</span>
      </li>
      <li class="contacts__item">
        <svg class="contacts__icon" viewBox="0 0 20 20" aria-hidden="true">
          <g fill="none" stroke="var(--accent)" stroke-width="1.4">
            <circle cx="10" cy="10" r="8.5"/>
            <ellipse cx="10" cy="10" rx="3.8" ry="8.5"/>
            <line x1="1.5" y1="10" x2="18.5" y2="10"/>
            <line x1="3" y1="5.5" x2="17" y2="5.5"/>
            <line x1="3" y1="14.5" x2="17" y2="14.5"/>
          </g>
        </svg>
        <span>www.harborbuilders.example</span>
      </li>
      <li class="contacts__item">
        <svg class="contacts__icon" viewBox="0 0 20 20" aria-hidden="true">
          <path d="M10 1 C5.8 1 3.5 4 3.5 7.4 C3.5 12 10 19 10 19 C10 19 16.5 12 16.5 7.4 C16.5 4 14.2 1 10 1 Z" fill="var(--accent)"/>
          <circle cx="10" cy="7.5" r="2.6" fill="#fff"/>
        </svg>
        <span>PO Box 1208 Eastgate LPO Riverton WA 6999</span>
      </li>
      <li class="contacts__legal">Registration 40517 ABN: 12 345 678 901</li>
    </ul>
  </section>

  <section class="card card--back" aria-label="Business card back">
    <div class="brand brand--back">
      <span class="brand__square"></span>
      <span class="brand__name">Harbor Builders</span>
    </div>
  </section>
</body>
</html>
```